Corporate Solar Marketing Presentation

We need a powerpoint presentation for a new product we are marketing in New York which is remote solar energy. We develop renewable energy solutions for large commercial customers. This new product, "Halvern Offsite Sunshare Plan" allows us to sell solar energy to customers remotely from a solar array located in the same general area as the customer.

We would like to see very sleek designs that use our logo and color scheme which is based on black. The final design should communicate trust, professionalism, and opportunity.

- The outline to start from is the file named "2015-11-23_marketing materials draft". This file outline the PPT and shows what we would like to see for basic content and graphics.

- the file named "logo" is our company logo and a good basis for the color theme of the presentation

- the third and fourth files are some stock photography we have purchased that you can use if helpful

- the fifth file "KVGRA Load Zones" corresponds to the graphic on page 4 of the outline. The figure should be the state map of NY and the blue shaded Area from "KVGRA Load Zones" is what we are trying outline on page 4 of the outline

- the sixth file "2015-10-07_Tamberly corporate overview" is the content that should be used to form page 3 on the outline titles About Tamberly Renewables. From the file use page 1 on the top half of the page, and on the bottom half of the page, include little icons for the following text labels (Development, Engineering, Construction, Finance, Operation & Maintenance)

Target Market(s)

High level decision makers at large corporations

Industry/Entity Type

Solar Energy

Font styles to use
Sans Serif

Colors
acd036
1b1b1b
7f7f7f
333333

Requirements
Must have
• - A draft design for each page in the outline

```html
<!DOCTYPE html>
<html lang="en">
<head>
<meta charset="utf-8">
<title>Tamberly Renewables – Halvern Offsite Sunshare Plan</title>
<link href="https://fonts.googleapis.com/css2?family=Russo+One&family=Roboto+Condensed:wght@400;700&family=Oswald:wght@300;400&display=swap" rel="stylesheet">
<style>
  :root{
    --lime:#acd036;
    --leaf:#6b9a1c;
    --ink:#1b1b1b;
    --black:#000;
    --grey:#7f7f7f;
    --charcoal:#333333;
    --bar:#e2e2e2;
    --paper:#ffffff;
    --forest:#2f5a1a;
    --pink:#d1195a;
    --navy:#1c2b6b;
    --head:"Russo One", sans-serif;
    --body:"Oswald", "Roboto Condensed", sans-serif;
    --small:"Roboto Condensed", sans-serif;
  }
  *{box-sizing:border-box;margin:0;padding:0}
  html,body{width:1200px;height:1200px;overflow:hidden;background:var(--paper)}
  .deck{position:relative;width:1200px;height:1200px}
  .slide{position:absolute;width:358px;height:210px;overflow:hidden;color:#fff;font-family:var(--body);font-weight:300;
    background:radial-gradient(ellipse 90% 110% at 0% 100%, #3f6d24 0%, #1f3d13 35%, #050805 75%, #000 100%)}
  .slide.dark{background:linear-gradient(90deg,#1e3a12 0%,#0a120a 45%,#000 100%)}
  .topbar{position:absolute;left:0;top:0;height:24px;background:var(--bar);color:var(--ink);font-family:var(--head);font-size:9px;
    display:flex;align-items:center;padding-left:12px;letter-spacing:.2px}
  .topbar.center{justify-content:center;padding-left:0;padding-right:40px}
  .abs{position:absolute}
  .tc{text-align:center}
  /* title slide */
  .cover-head{position:absolute;left:0;top:0;width:358px;height:77px;background:#000}
  .cover-title{top:27px;left:0;width:358px;text-align:center;font-family:var(--head);font-size:17px}
  .cover-sub{top:50px;left:0;width:358px;text-align:center;font-size:11px;font-weight:400}
  .cover-photo{position:absolute;left:0;top:77px;width:358px;height:133px;
    background:linear-gradient(90deg,#3c7a2a 0%,#6f9fc2 35%,#8aa6bd 60%,#2a3f5c 100%)}
  .brand-box{position:absolute;left:84px;top:99px;width:189px;height:92px;background:#000;border:2px solid #fff;
    display:flex;align-items:center;justify-content:center;font-family:var(--body);font-weight:400;font-size:30px;letter-spacing:6px}
  /* highlights */
  .hl-row{position:absolute;left:22px;display:flex;align-items:center;gap:14px;font-size:12px;line-height:1.25}
  .hl-icon{width:32px;height:32px;flex:none}
  .globe{position:absolute;right:-30px;top:80px;width:200px;height:200px;border-radius:50%;
    background:radial-gradient(circle at 40% 40%,#1f3a18,#0b140b 70%)}
  /* about */
  .about-para{top:37px;left:40px;width:278px;font-size:6.6px;line-height:1.35;text-align:center;font-weight:400}
  .about-col{position:absolute;top:80px;width:88px}
  .about-col h4{font-family:var(--head);font-weight:400;font-size:5.6px;text-align:center;background:#000;padding:1px 0}
  .about-col p{background:var(--leaf);border-radius:3px;height:80px;padding:3px;font-family:var(--small);font-size:3.7px;line-height:1.3;text-align:center}
  .pin-label{position:absolute;top:190px;width:62px;height:7px;font-family:var(--small);font-weight:700;font-size:4.5px;text-align:center;line-height:7px}
  /* part 1 */
  .intro{top:30px;left:30px;width:298px;text-align:center;font-size:8.5px;line-height:1.4;font-weight:400}
  .map-ph{position:absolute;border-radius:4px}
  .zone-tag{position:absolute;font-family:var(--small);font-weight:700;font-size:4px;text-align:center;color:#1d2a9a;padding:2px}
  /* part 2 */
  .flow{font-size:7.4px;line-height:1.3;font-weight:400}
  .flow-box{position:absolute;background:#f2f2f2;color:var(--ink);font-family:var(--small);font-size:5.4px;display:flex;align-items:center;justify-content:center}
  .brand-mini{position:absolute;left:140px;top:48px;width:70px;height:20px;background:#000;border:1px solid #fff;font-size:9px;font-weight:400;letter-spacing:2px;display:flex;align-items:center;justify-content:center}
  /* part 3 */
  .cost-banner{position:absolute;left:63px;top:44px;width:108px;height:18px;background:var(--leaf);color:var(--lime);font-size:11px;font-weight:400;display:flex;align-items:center;justify-content:center}
  .cost-table{position:absolute;left:28px;top:67px;width:193px;border-collapse:collapse;background:#e9e9e9;color:var(--charcoal);font-family:var(--small);font-size:5.6px}
  .cost-table td{border:1px solid #c9c9c9;height:15px;text-align:center}
  .cost-table td.num{width:34px}
  .note{font-size:6.2px;line-height:1.3;font-weight:400;text-align:center}
  .mini-rates{font-family:var(--small);font-size:4.4px;line-height:1.55}
  /* chart */
  .axis-label{font-size:7px;font-weight:400}
  /* solar */
  .bulb-photo{position:absolute;border-radius:48% 52% 50% 50%}
  /* timeline */
  .tag{position:absolute;background:var(--leaf);color:#fff;font-size:7px;padding:0 2px;font-weight:400}
  .tl{position:absolute;font-size:7px;font-weight:400;line-height:1.3}
  /* faq */
  .qa-card{position:absolute;width:110px;height:26px;background:linear-gradient(#ffffff,#d9d9d9);color:var(--ink);font-family:var(--small);font-size:6.5px;line-height:1.25;padding:2px 4px;border-left:1px solid #999}
</style>
</head>
<body>
<main class="deck">

  <!-- 1 Cover -->
  <section class="slide" style="left:34px;top:116px">
    <div class="cover-head"></div>
    <div class="abs cover-title">Tamberly Renewables</div>
    <div class="abs cover-sub">Halvern Offsite Sunshare Plan</div>
    <div class="cover-photo" role="img" aria-label="Solar panels on grass under a blue sky, framed in a light bulb shape"></div>
    <div class="brand-box">TAMBERLY</div>
  </section>

  <!-- 2 Program highlights -->
  <section class="slide" style="left:417px;top:116px;background:#000">
    <div class="topbar" style="width:150px;clip-path:polygon(0 0,100% 0,88% 100%,0 100%)">PROGRAM HIGHLIGHTS</div>
    <div class="globe" role="img" aria-label="Faint dark green globe"></div>
    <div class="hl-row" style="top:58px">
      <svg class="hl-icon" viewBox="0 0 32 32"><rect x="3" y="12" width="22" height="13" rx="2" fill="#8fbf3a"/><rect x="7" y="7" width="22" height="13" rx="2" fill="#acd036"/><circle cx="18" cy="13.5" r="3.5" fill="#6b9a1c"/></svg>
      <span>Significant electric savings and long term cost<br>stability with no upfront investment</span>
    </div>
    <div class="hl-row" style="top:100px">
      <svg class="hl-icon" viewBox="0 0 32 32"><rect x="9" y="3" width="14" height="26" fill="#3e9a4a"/><g fill="#acd036"><rect x="11" y="6" width="3" height="3"/><rect x="18" y="6" width="3" height="3"/><rect x="11" y="12" width="3" height="3"/><rect x="18" y="12" width="3" height="3"/><rect x="11" y="18" width="3" height="3"/><rect x="18" y="18" width="3" height="3"/></g><rect x="2" y="28" width="28" height="2" fill="#2d6a2e"/></svg>
      <span>No impact to on site property and operations</span>
    </div>
    <div class="hl-row" style="top:136px">
      <svg class="hl-icon" viewBox="0 0 32 32"><polygon points="16,2 29,9 29,23 16,30 3,23 3,9" fill="#fff"/><polygon points="16,5 26,11 26,21 16,27 6,21 6,11" fill="#5aa02c"/><path d="M16 22 C10 18 11 12 16 10 C21 12 22 18 16 22Z" fill="#fff"/></svg>
      <span>Positive environmental impact</span>
    </div>
  </section>

  <!-- 3 About -->
  <section class="slide" style="left:799px;top:116px">
    <div class="topbar" style="width:152px;clip-path:polygon(0 0,100% 0,91% 100%,0 100%)">ABOUT TAMBERLY RENEWABLES</div>
    <p class="abs about-para">Tamberly is a renewable power company focused on greenfield development and M&amp;A opportunities in the North American solar and wind sectors. Tamberly is also continuously evaluating the market to partner with experienced teams to pursue opportunities employing other renewable power technologies.</p>
    <svg class="abs" style="left:30px;top:86px" width="328" height="74" viewBox="0 0 328 74"><polygon points="0,14 300,14 300,0 328,37 300,74 300,60 0,60" fill="#5d5d5d"/></svg>
    <div class="about-col" style="left:35px"><h4>OVERVIEW</h4><p>Tamberly was established by Ashgrove Capital through its second energy fund. Its initial focus is on commercial and industrial distributed generation and residential deployment of solar, with plans to expand into utility-scale solar and wind.</p></div>
    <div class="about-col" style="left:133px"><h4>TRACK RECORD</h4><p>Our management experience comes from a company that developed over 140 MW of commercial and industrial solar. The team has over 100 years of collective experience across projects in the United States.</p></div>
    <div class="about-col" style="left:230px"><h4>CAPABILITIES</h4><p>As a company focused on solar, we provide capabilities to build and finance residential, commercial and utility-scale projects. Engineering, Procurement and Construction. Project Development. Finance. Operation and Maintenance.</p></div>
    <svg class="abs" style="left:0;top:170px" width="358" height="20" viewBox="0 0 358 20">
      <g fill="#8fbf3a"><path d="M70 0a7 7 0 0 1 7 7c0 5-7 12-7 12s-7-7-7-12a7 7 0 0 1 7-7z"/><path d="M140 0a7 7 0 0 1 7 7c0 5-7 12-7 12s-7-7-7-12a7 7 0 0 1 7-7z"/><path d="M213 0a7 7 0 0 1 7 7c0 5-7 12-7 12s-7-7-7-12a7 7 0 0 1 7-7z"/><path d="M283 0a7 7 0 0 1 7 7c0 5-7 12-7 12s-7-7-7-12a7 7 0 0 1 7-7z"/></g>
      <g fill="#fff"><circle cx="70" cy="7" r="2.6"/><circle cx="140" cy="7" r="2.6"/><circle cx="213" cy="7" r="2.6"/><circle cx="283" cy="7" r="2.6"/></g>
    </svg>
    <div class="pin-label" style="left:39px;background:#000">Development &amp; Engineering</div>
    <div class="pin-label" style="left:109px;background:var(--pink)">Construction</div>
    <div class="pin-label" style="left:182px;background:var(--navy)">Financing</div>
    <div class="pin-label" style="left:252px;background:#2aa84a">Operation</div>
  </section>

  <!-- 4 Part 1 -->
  <section class="slide" style="left:34px;top:347px">
    <div class="topbar" style="width:270px;background:var(--bar);clip-path:polygon(0 0,100% 0,92% 100%,0 100%);padding-left:6px">NY REMOTE NET METERING – HOW IT WORKS: PART 1</div>
    <p class="abs intro">As a NYS Utility Customer, you can purchase power from any of our remotely located solar systems located in the same Load Zone and Utility Territory.</p>
    <div class="map-ph" style="left:26px;top:64px;width:160px;height:125px;background:linear-gradient(135deg,#1f3fd6 0%,#e01c1c 40%,#35d0c8 70%,#1f3fd6 100%);opacity:.85" role="img" aria-label="Map of New York State colour-coded by KVGRA load zone"></div>
    <div class="map-ph" style="left:196px;top:64px;width:154px;height:122px;background:linear-gradient(135deg,#f4f4f4,#cfcfcf)" role="img" aria-label="Map of New York State with utility territory boundaries"></div>
    <div class="zone-tag" style="left:26px;top:70px;width:64px;background:#f2f23a">NEW YORK CONTROL AREA LOAD ZONES</div>
    <div class="zone-tag" style="left:196px;top:68px;width:64px;background:#fff">NEW YORK CONTROL AREA LOAD ZONES</div>
  </section>

  <!-- 5 Part 2 -->
  <section class="slide" style="left:417px;top:347px">
    <div class="topbar" style="width:270px;clip-path:polygon(0 0,100% 0,92% 100%,0 100%);padding-left:6px">NY REMOTE NET METERING – HOW IT WORKS: PART 2</div>
    <div class="abs flow tc" style="left:110px;top:33px;width:130px">Funds and owns the solar system</div>
    <div class="brand-mini">TAMBERLY</div>
    <div class="abs flow tc" style="left:20px;top:59px;width:110px">System sized to produce up<br>to 100% of your annual<br>consumption</div>
    <div class="abs flow tc" style="left:240px;top:59px;width:110px">You pay Tamberly a fixed rate<br>of $0.11/kWh for every<br>kWh produced</div>
    <div class="abs" style="left:38px;top:92px;width:90px;height:65px;border-radius:40% 60% 50% 50%;background:linear-gradient(135deg,#6fa2cf,#3d7a2a)" role="img" aria-label="Solar panels inside a light bulb held in a hand"></div>
    <svg class="abs" style="left:0;top:0" width="358" height="210" viewBox="0 0 358 210">
      <defs><marker id="ah" markerWidth="6" markerHeight="6" refX="5" refY="3" orient="auto"><path d="M0,0 L6,3 L0,6Z" fill="#fff"/></marker></defs>
      <g stroke="#fff" stroke-width="1" fill="none">
        <line x1="140" y1="60" x2="118" y2="88" marker-end="url(#ah)"/>
        <line x1="212" y1="60" x2="232" y2="84" marker-end="url(#ah)"/>
        <line x1="262" y1="108" x2="275" y2="118" marker-end="url(#ah)"/>
        <line x1="275" y1="142" x2="258" y2="155" marker-end="url(#ah)"/>
        <line x1="232" y1="165" x2="203" y2="170" marker-end="url(#ah)"/>
        <line x1="120" y1="125" x2="158" y2="160" marker-end="url(#ah)"/>
      </g>
      <rect x="228" y="88" width="22" height="18" fill="#c58f8f"/><rect x="235" y="82" width="22" height="18" fill="#9a6b6b"/>
      <rect x="222" y="155" width="22" height="14" fill="#8fbf3a"/><rect x="228" y="149" width="22" height="14" fill="#acd036"/>
    </svg>
    <div class="flow-box" style="left:273px;top:118px;width:42px;height:22px">Client Logo</div>
    <div class="flow-box" style="left:160px;top:163px;width:42px;height:20px">Northway Grid</div>
    <div class="abs flow tc" style="left:40px;top:174px;width:120px">Tamberly provides all kWh generated<br>directly to the utility grid</div>
    <div class="abs flow tc" style="left:210px;top:174px;width:145px">The utility provides you with an on bill $ credit<br>equal to the kWh generated * Retail Rate</div>
  </section>

  <!-- 6 Part 3 -->
  <section class="slide" style="left:799px;top:347px">
    <div class="topbar" style="width:270px;clip-path:polygon(0 0,100% 0,92% 100%,0 100%);padding-left:4px">NY REMOTE NET METERING – HOW IT WORKS: PART 3</div>
    <div class="cost-banner">YOUR ELECTRIC COST</div>
    <table class="cost-table">
      <tr><td>Current Electric Bill</td><td class="num">$100,000</td></tr>
      <tr><td>(-) Solar Credits (500,000 kWh x 0.134)</td><td class="num">$67,000</td></tr>
      <tr><td>New Utility Bill</td><td class="num">$33,000</td></tr>
      <tr><td>(+) Tamberly Post Cost (500,000 kWh x $0.11)</td><td class="num">$55,000</td></tr>
      <tr><td>New Electric Cost</td><td class="num">$88,000</td></tr>
      <tr><td>Annual Savings ($)</td><td class="num">12,000</td></tr>
      <tr><td>Annual Savings (%)</td><td class="num">12%</td></tr>
    </table>
    <p class="abs note" style="left:238px;top:38px;width:115px">The net metering is calculated based on Rate class “small commercial Non Renew” which is defined by the utility and fluctuates over time.</p>
    <div class="abs mini-rates" style="left:246px;top:82px">Current &nbsp;&nbsp;&nbsp;&nbsp; NMC<br>(+) Supply &nbsp; $0.065<br>(+) Delivery &nbsp;$0.053<br>(+) Other &nbsp;&nbsp;&nbsp;$0.042<br>&nbsp;&nbsp;&nbsp;&nbsp;Total &nbsp;&nbsp;&nbsp;&nbsp;$0.134</div>
    <div class="abs mini-rates" style="left:307px;top:92px;width:40px">* Only offsites kWh based channels</div>
    <p class="abs note" style="left:238px;top:140px;width:115px">Tamberly post cost is fixed under the BOH contract. As utility rates escalate over time at a higher rate than your BOH, you’re $ savings increase billing to keep your overall utility bill flat.</p>
    <svg class="abs" style="left:0;top:0" width="358" height="210" viewBox="0 0 358 210">
      <defs><marker id="ah2" markerWidth="6" markerHeight="6" refX="5" refY="3" orient="auto"><path d="M0,0 L6,3 L0,6Z" fill="#fff"/></marker></defs>
      <g stroke="#fff" stroke-width="1.2"><line x1="221" y1="73" x2="254" y2="63" marker-end="url(#ah2)"/><line x1="221" y1="131" x2="254" y2="140" marker-end="url(#ah2)"/></g>
    </svg>
  </section>

  <!-- 7 Hedge chart -->
  <section class="slide dark" style="left:34px;top:582px">
    <div class="topbar" style="width:270px;clip-path:polygon(0 0,100% 0,92% 100%,0 100%);padding-left:8px">SOLAR PPA: A HEDGE AGAINST FUTURE RATE INCREASES</div>
    <svg class="abs" style="left:0;top:0" width="358" height="210" viewBox="0 0 358 210">
      <line x1="27" y1="40" x2="27" y2="175" stroke="#6b9a1c" stroke-width="3"/>
      <line x1="26" y1="175" x2="332" y2="175" stroke="#6b9a1c" stroke-width="3"/>
      <line x1="27" y1="102" x2="318" y2="50" stroke="#fff" stroke-width="1.6"/>
      <line x1="27" y1="102" x2="322" y2="88" stroke="#fff" stroke-width="1.6" stroke-dasharray="4 3"/>
      <path d="M198 76 q3 0 3 4 v4 q0 3 3 3 q-3 0 -3 3 v4 q0 4 -3 4" stroke="#fff" fill="none" stroke-width="1"/>
    </svg>
    <div class="abs axis-label" style="left:280px;top:40px">Retail Rate</div>
    <div class="abs axis-label" style="left:207px;top:78px">Day 1 Savings</div>
    <div class="abs axis-label" style="left:286px;top:95px">PPH Rate</div>
    <div class="abs axis-label" style="left:58px;top:182px">1998</div>
    <div class="abs axis-label" style="left:110px;top:182px">2005</div>
    <div class="abs axis-label" style="left:163px;top:182px">2015</div>
    <div class="abs axis-label" style="left:304px;top:182px">2035</div>
  </section>

  <!-- 8 Your solar system -->
  <section class="slide" style="left:417px;top:582px;background:radial-gradient(ellipse 80% 90% at 55% 35%,#2f5a5a 0%,#1d3a3a 45%,#0c1616 100%)">
    <div class="topbar center" style="width:264px;clip-path:polygon(0 0,100% 0,89% 100%,0 100%)">YOUR SOLAR SYSTEM</div>
    <div class="bulb-photo" style="left:6px;top:60px;width:140px;height:120px;background:linear-gradient(160deg,#5e95d0 0%,#a6c3dd 35%,#3c5c7a 55%,#4b8a2a 85%)" role="img" aria-label="Solar array on green grass inside a light bulb silhouette"></div>
  </section>

  <!-- 9 Timeline -->
  <section class="slide dark" style="left:799px;top:582px">
    <div class="topbar center" style="width:264px;clip-path:polygon(0 0,100% 0,89% 100%,0 100%)">PROJECT TIMELINE</div>
    <svg class="abs" style="left:0;top:0" width="358" height="210" viewBox="0 0 358 210">
      <defs><marker id="ah3" markerWidth="6" markerHeight="6" refX="5" refY="3" orient="auto"><path d="M0,0 L6,3 L0,6Z" fill="#fff"/></marker></defs>
      <circle cx="48" cy="108" r="25" fill="#d9d9d9"/><circle cx="48" cy="108" r="20" fill="#fff"/>
      <text x="48" y="116" text-anchor="middle" font-family="Russo One, sans-serif" font-size="20" fill="#e8a21a">$</text>
      <line x1="48" y1="108" x2="48" y2="93" stroke="#333" stroke-width="1.5"/>
      <line x1="90" y1="99" x2="138" y2="99" stroke="#fff" stroke-width="1"/>
      <polygon points="140,90 142.4,96.6 149.5,96.9 143.9,101.2 145.9,108 140,104 134.1,108 136.1,101.2 130.5,96.9 137.6,96.6" fill="#fff"/>
      <line x1="80" y1="125" x2="140" y2="125" stroke="#fff" stroke-width="1.2" stroke-dasharray="3 2"/>
      <line x1="178" y1="145" x2="245" y2="145" stroke="#fff" stroke-width="1" marker-end="url(#ah3)"/>
      <line x1="265" y1="171" x2="330" y2="171" stroke="#fff" stroke-width="1" marker-end="url(#ah3)"/>
    </svg>
    <div class="tag" style="left:161px;top:62px">Feb 2016</div>
    <div class="tag" style="left:229px;top:62px">August 2016</div>
    <div class="tl" style="left:90px;top:86px">Dana Corwell</div>
    <div class="tl" style="left:155px;top:86px">Execute PPA</div>
    <div class="tl" style="left:82px;top:111px">Tamberly Project Dev</div>
    <div class="tl tc" style="left:172px;top:120px;width:80px">Tamberly Constructive and<br>Interconnection</div>
    <div class="tl tc" style="left:262px;top:148px;width:70px">Commercial Operate<br>Start Saving $$</div>
  </section>

  <!-- 10 FAQ -->
  <section class="slide" style="left:34px;top:814px">
    <div class="topbar center" style="width:264px;clip-path:polygon(0 0,100% 0,89% 100%,0 100%)">FAQ</div>
    <svg class="abs" style="left:0;top:0" width="358" height="210" viewBox="0 0 358 210">
      <polygon points="86,48 286,48 298,59 286,70 86,70" fill="#6b9a1c"/>
      <g fill="#9b9b9b"><circle cx="73" cy="48" r="9"/><circle cx="91" cy="47" r="9"/><circle cx="69" cy="62" r="9"/><circle cx="94" cy="63" r="9"/></g>
      <g font-family="Roboto Condensed, sans-serif" font-size="9" fill="#fff" text-anchor="middle"><text x="73" y="51">?</text><text x="91" y="50">?</text><text x="69" y="65">?</text><text x="94" y="66">?</text></g>
      <text x="190" y="64" text-anchor="middle" font-family="Oswald, sans-serif" font-size="14" fill="#fff">Q&amp;A</text>
    </svg>
    <div class="qa-card" style="left:64px;top:81px">Q:<br>A:</div>
    <div class="qa-card" style="left:182px;top:81px">Q:<br>A:</div>
    <div class="qa-card" style="left:64px;top:110px">Q:<br>A:</div>
    <div class="qa-card" style="left:182px;top:110px">Q:<br>A:</div>
    <div class="qa-card" style="left:64px;top:140px">Q:<br>A:</div>
    <div class="qa-card" style="left:182px;top:140px">Q:<br>A:</div>
    <div class="qa-card" style="left:64px;top:169px">Q:<br>A:</div>
    <div class="qa-card" style="left:182px;top:169px">Q:<br>A:</div>
  </section>

  <!-- 11 Environmental impact -->
  <section class="slide dark" style="left:417px;top:814px">
    <div class="topbar" style="width:270px;padding-left:76px;clip-path:polygon(0 0,100% 0,92% 100%,0 100%)">ENVIRONMENTAL IMPACT</div>
    <svg class="abs" style="left:58px;top:0" width="16" height="26" viewBox="0 0 16 26"><path d="M8 25 C0 18 1 6 12 1 C15 10 15 19 8 25Z" fill="#5aa02c"/><path d="M8 25 C9 16 10 9 12 2" stroke="#2d5c14" stroke-width="0.8" fill="none"/></svg>
  </section>

</main>
</body>
</html>
```